Gobal construction supply company needs new business card design

I need a business card design for my global supply company using an existing logo. i will be looking to print these on rounded corner cards with the black background version of my logo on the back. on the front white background, my logo again and my simple details.

```html
<!DOCTYPE html>
<html lang="en">
<head>
<meta charset="utf-8">
<title>Meridian Builders Supply – Business Cards</title>
<link href="https://fonts.googleapis.com/css2?family=Roboto:wght@400;500;700&display=swap" rel="stylesheet">
<style>
  :root {
    --backdrop: #2a2a2b;
    --card-black: #1c1b1d;
    --card-white: #ffffff;
    --ink: #262626;
    --ink-soft: #3a3a3a;
    --brand-red: #e3212b;
    --rule-grey: #7a7a7a;
  }
  * { box-sizing: border-box; margin: 0; padding: 0; }
  html, body {
    width: 1200px; height: 930px; overflow: hidden;
    background: var(--backdrop);
    font-family: "Roboto", Arial, sans-serif;
  }
  .canvas { position: relative; width: 1200px; height: 930px; }

  .card {
    position: absolute; width: 560px; height: 320px;
    border-radius: 18px; overflow: hidden;
  }

  /* Back of card */
  .card-back { left: 110px; top: 90px; background: var(--card-black); }
  .card-back .world-map {
    position: absolute; left: 40px; top: 40px; width: 480px; height: 240px;
    background: radial-gradient(ellipse at center, rgba(255,255,255,0.09), rgba(255,255,255,0) 70%);
  }
  .card-back .brand-lockup {
    position: absolute; left: 0; right: 0; top: 132px;
    display: flex; flex-direction: column; align-items: center; gap: 14px;
  }
  .brand-row { display: flex; align-items: center; gap: 12px; }
  .brand-mark { width: 22px; height: 22px; background: var(--brand-red); }
  .brand-name {
    font-weight: 700; font-size: 27px; letter-spacing: 0.5px; text-transform: uppercase;
  }
  .card-back .brand-name { color: #ffffff; }
  .brand-rule { width: 360px; height: 2px; background: var(--brand-red); }

  /* Front of card */
  .card-front { left: 530px; top: 480px; background: var(--card-white); }
  .card-front .brand-lockup {
    position: absolute; left: 24px; top: 112px; width: 270px;
    display: flex; flex-direction: column; align-items: center; gap: 12px;
  }
  .card-front .brand-name { color: var(--ink); font-size: 17px; }
  .card-front .brand-mark { width: 16px; height: 16px; }
  .card-front .brand-rule { width: 240px; }

  .divider {
    position: absolute; left: 305px; top: 52px; width: 1px; height: 136px;
    background: var(--rule-grey);
  }
  .contact { position: absolute; left: 322px; top: 42px; color: var(--ink-soft); }
  .contact .person-name {
    color: var(--brand-red); font-size: 21px; font-weight: 500; text-transform: uppercase;
  }
  .contact .person-title { font-size: 12.5px; margin-top: 2px; }
  .contact .address { font-size: 12.5px; line-height: 1.35; margin-top: 12px; }
  .contact-list { list-style: none; margin-top: 8px; font-size: 12.5px; line-height: 1.45; }
  .contact-list li { display: flex; align-items: center; gap: 7px; }
  .contact-list svg { width: 10px; height: 10px; flex: none; }
  .contact-list .accent { color: var(--brand-red); }

  .swoosh { position: absolute; left: 0; bottom: 0; width: 560px; height: 108px; }
</style>
</head>
<body>
<main class="canvas">

  <section class="card card-back" aria-label="Business card back">
    <div class="world-map" role="img" aria-label="Faint dotted world map"></div>
    <div class="brand-lockup">
      <div class="brand-row">
        <span class="brand-mark"></span>
        <span class="brand-name">Meridian Builders Supply</span>
      </div>
      <div class="brand-rule"></div>
    </div>
  </section>

  <section class="card card-front" aria-label="Business card front">
    <div class="brand-lockup">
      <div class="brand-row">
        <span class="brand-mark"></span>
        <span class="brand-name">Meridian Builders Supply</span>
      </div>
      <div class="brand-rule"></div>
    </div>

    <div class="divider"></div>

    <div class="contact">
      <p class="person-name">Daniel Harlow</p>
      <p class="person-title">Director</p>
      <p class="address">48 Quarry Road Unit 12<br>Stonebridge, AB</p>
      <ul class="contact-list">
        <li>
          <svg viewBox="0 0 10 10"><path d="M2 1 L4 1 L4.6 3 L3.5 3.8 Q4.5 5.8 6.2 6.5 L7 5.4 L9 6 L9 8 Q5 9 1 2 Z" fill="var(--brand-red)"/></svg>
          403-555-0182
        </li>
        <li>
          <svg viewBox="0 0 10 10"><rect x="0.8" y="2" width="8.4" height="6" fill="none" stroke="var(--brand-red)" stroke-width="1"/><path d="M1 2.3 L5 5.5 L9 2.3" fill="none" stroke="var(--brand-red)" stroke-width="1"/></svg>
          hello@meridianbuild.com
        </li>
        <li>
          <svg viewBox="0 0 10 10"><circle cx="5" cy="5" r="4" fill="none" stroke="var(--brand-red)" stroke-width="1"/><path d="M1 5 H9 M5 1 Q2.5 5 5 9 M5 1 Q7.5 5 5 9" fill="none" stroke="var(--brand-red)" stroke-width="0.8"/></svg>
          www.<span class="accent">meridianbuild</span>.com
        </li>
      </ul>
    </div>

    <svg class="swoosh" viewBox="0 0 560 108" preserveAspectRatio="none" aria-hidden="true">
      <path d="M0 108 L0 100 C150 94 260 36 400 20 C470 13 520 14 560 16 L560 108 Z" fill="var(--card-black)"/>
      <path d="M0 95 C150 89 260 31 400 14 C470 7 520 8 560 10" fill="none" stroke="var(--brand-red)" stroke-width="4.5"/>
      <path d="M0 88 C150 82 260 25 400 8 C470 1 520 2 560 4" fill="none" stroke="var(--brand-red)" stroke-width="1"/>
    </svg>
  </section>

</main>
</body>
</html>
```